Brightfield Program (8 x 8) to be posted on Facebook, Twitter & Instagram

YOUR NEW HOME PURCHASE IS BRIGHTFIELD BOUND
with the
HLB BRIGHTFIELD 2.0 PROGRAM
* Up to 5% Assistance with 640 Score
* Up to 6% Assistance with 660 Score
* Also 6% Seller Help Allowed
Call to be Pre-Qualified Today!
(800) 417-2960
Copperline Financial Services, Inc.
7120 Marlow Brook Road, Harlow Springs, VA 22190
www.copperlinelending.com
LRID #731586

```html
<!DOCTYPE html>
<html lang="en">
<head>
<meta charset="utf-8">
<title>Brightfield Program</title>
<link rel="stylesheet" href="https://fonts.googleapis.com/css2?family=Montserrat:wght@500;600;700;800&family=Oswald:wght@500&display=swap">
<style>
  :root {
    --blue: #0b65a9;
    --gold: #b5a553;
    --gold-text: #ad9b4c;
    --white: #ffffff;
    --rule: #8a8a8a;
    --photo-top: #c9c4b8;
    --photo-mid: #a9a596;
    --photo-low: #5f8a3a;
  }
  * { margin: 0; padding: 0; box-sizing: border-box; }
  html, body { width: 1200px; height: 1200px; overflow: hidden; background: var(--white); }
  .ad { position: relative; width: 1200px; height: 1200px; background: var(--white); font-family: "Montserrat", sans-serif; }
  .shapes { position: absolute; inset: 0; }
  .headline { position: absolute; left: 52px; top: 138px; color: var(--white); font-weight: 800; font-size: 55px; line-height: 60px; letter-spacing: -0.5px; }
  .with-the { position: absolute; left: 56px; top: 398px; color: var(--white); font-weight: 500; font-size: 38px; }
  .program { position: absolute; left: 54px; top: 478px; color: var(--white); font-weight: 800; }
  .program .name { display: block; font-size: 44px; line-height: 52px; letter-spacing: -0.5px; }
  .program .version { display: block; font-size: 72px; line-height: 74px; letter-spacing: -1px; }
  .benefits { position: absolute; left: 57px; top: 690px; width: 390px; list-style: none; }
  .benefit { font-weight: 800; font-size: 29px; line-height: 33px; padding: 0 0 0 2px; }
  .benefit + .benefit { border-top: 2px solid var(--rule); margin-top: 14px; padding-top: 16px; }
  .benefit .lead { color: var(--blue); display: block; }
  .benefit .tail { color: var(--gold-text); display: block; }
  .brand { position: absolute; left: 835px; top: 172px; display: flex; align-items: center; gap: 12px; color: var(--blue); font-weight: 700; font-size: 22px; line-height: 26px; }
  .brand .dot { width: 34px; height: 34px; border-radius: 50%; background: var(--gold); flex: none; }
  .call { position: absolute; left: 0; top: 1004px; width: 242px; text-align: center; color: var(--white); font-family: "Oswald", sans-serif; font-weight: 500; }
  .call .small { display: block; font-size: 32px; line-height: 34px; letter-spacing: -0.5px; }
  .call .big { display: block; font-size: 56px; line-height: 66px; letter-spacing: -1px; }
  .contact { position: absolute; left: 280px; top: 1014px; width: 440px; text-align: center; color: var(--white); }
  .contact .phone { display: block; font-weight: 600; font-size: 58px; line-height: 68px; letter-spacing: -0.5px; }
  .contact .web { display: block; font-weight: 700; font-size: 23px; line-height: 32px; }
  .company { position: absolute; left: 782px; top: 1018px; width: 280px; color: var(--white); }
  .company .name { font-weight: 700; font-size: 20px; line-height: 26px; }
  .company .address { margin-top: 8px; font-weight: 500; font-size: 16.5px; line-height: 27px; letter-spacing: 0.2px; }
  .license { position: absolute; left: 1060px; top: 1122px; width: 124px; text-align: center; color: var(--white); font-weight: 500; font-size: 15px; }
</style>
</head>
<body>
<div class="ad">
  <svg class="shapes" width="1200" height="1200" viewBox="0 0 1200 1200">
    <defs>
      <linearGradient id="photoTone" x1="0" y1="0" x2="0" y2="1">
        <stop offset="0" stop-color="var(--photo-top)"/>
        <stop offset="0.55" stop-color="var(--photo-mid)"/>
        <stop offset="1" stop-color="var(--photo-low)"/>
      </linearGradient>
    </defs>
    <polygon class="hero-chevron" points="0,105 589,105 750,371 581,662 0,662" fill="var(--blue)"/>
    <polygon class="family-photo" role="img" aria-label="Photo of a smiling family in front of their new house holding a sold sign and a for sale by owner sign" points="750,371 1200,371 1200,994 398,994" fill="url(#photoTone)"/>
    <rect class="footer-band" x="0" y="994" width="1200" height="157" fill="var(--gold)"/>
    <polygon class="footer-chevron" points="229,994 720,994 759,1072 716,1151 229,1151 270,1072" fill="var(--blue)"/>
    <polyline points="223,994 264,1072 223,1151" fill="none" stroke="var(--white)" stroke-width="5"/>
    <polyline points="726,994 765,1072 722,1151" fill="none" stroke="var(--white)" stroke-width="5"/>
    <rect class="housing-badge" x="1068" y="1014" width="92" height="90" rx="4" fill="var(--white)" opacity="0.9"/>
  </svg>

  <div class="brand"><span class="dot"></span><span>Copperline<br>Financial Services, Inc.</span></div>

  <h1 class="headline">YOUR NEW<br>HOME PURCHASE<br>IS BRIGHTFIELD<br>BOUND</h1>
  <p class="with-the">with the</p>
  <h2 class="program"><span class="name">HLB BRIGHTFIELD</span><span class="version">2.0 PROGRAM</span></h2>

  <ul class="benefits">
    <li class="benefit"><span class="lead">* UP TO 5% ASSISTANCE</span><span class="tail">WITH 640 SCORE</span></li>
    <li class="benefit"><span class="lead">* UP TO 6% ASSISTANCE</span><span class="tail">WITH 660 SCORE</span></li>
    <li class="benefit"><span class="lead">&nbsp;* ALSO 6% SELLER</span><span class="tail">&nbsp;HELP ALLOWED</span></li>
  </ul>

  <p class="call"><span class="small">CALL TO BE</span><span class="small">PRE-QUALIFIED</span><span class="big">TODAY!</span></p>
  <p class="contact"><span class="phone">(800) 417-2960</span><span class="web">www.copperlinelending.com</span></p>
  <div class="company">
    <p class="name">Copperline<br>Financial Services, Inc.</p>
    <p class="address">7120 Marlow Brook Road,<br>Harlow Springs, VA 22190</p>
  </div>
  <p class="license">LRID #731586</p>
</div>
</body>
</html>
```